Etiketten für Ätherische Öle, Extrakte und Speiseöle gesucht
Zielgruppe
Wir verkaufen natürlich Produkte. Ätherische öle, Extrakte, Speise öle.
Wir verkaufen im Webshop, Korbix und auch im Betrieb.
https://www.natur-vemo.com
Wir verkaufen hauptsächlich innerhalb Italiens und Deutschland daher doppel sprachig.
Aufgabenstellung
Guten Tag
Bitte verwenden Sie! : * beispiel_10_ml_etikett_nachbau.jpg *
Da mir die kleinste Größe die wichtigste ist habe ich ein beispiel Hochgeladen. Das kleinste Etikett lässt sich öffnen und daher sind nur 7 cm ersichtlich und man muss das Etikett aufmachen.
Habe ein Beispiel Hochgeladen. Aber bitte einfach kreativ sein. *Anhang: beispiel Etikett*
Sobald ich eine Art vom kelinsten habe würde ich dies für die 2 anderen Größen übernehmen aber das man Sie irgendwie gut unterscheiden kann da dies dann komplett andere Produkte (Extrakte/Speise öl) sein werden.
Erstellung von drei unterschiedlichen Größen von Etiketten mit folgenden Eigenschaften:
Am wichtigsten ist mir das kleinste Etikett da dies auch am schwersten ist daher habe ich die anderen Größen nun gelöscht!
• 10 ml Länge: 155 mm Breite: 32 mm.
Brauche 3 unterschiedliche Grund Farben: z. B. Ätherische Öle (Grün) Extrakte (Rot) Speiseöle (gelb). Die Farben lasse ich sie entscheiden.
Die Etiketten müssen 2 Sprachen (Deutsch / Italienisch) sein deshalb muss dieses berücksichtigt werden.
Anbei finden Sie:
• Logo (Bild Logo)
• Beispiel Text ätherische Öle
• Bilder der aktuellen Flaschen
Unter https://www.natur-vemo.com/de finden Sie meine Seite
Anmerkung: Im Anhang: *Back*
Habe ich mein Logo mit Firmennamen ; Bio des Haubner Stefan
Da ich jedoch nicht alle Produkte im biologischen Anbau habe und mein Logo zu miss Verständnis führen könnte habe ich ein Bildliches Logo gemacht das ich fortan auf meinen Produkten haben möchte. Im besonderes dieses Grün das in beiden vorhanden ist versuche ich zu integrieren.
Habe selbst ein Etikett designet das aber sehr unprofessionell wirkt aber dieses Grüne das ich gerne als merkmal unterbringen würde.
Siehe Anhang: neemöl

```html
<!DOCTYPE html>
<html lang="de">
<head>
<meta charset="utf-8">
<title>Etikett Lavendel 10 ml</title>
<link href="https://fonts.googleapis.com/css2?family=Arimo:wght@400;700&family=Poppins:wght@300;400&display=swap" rel="stylesheet">
<style>
  :root {
    --paper: #ffffff;
    --ink: #1a1a1a;
    --cut-line: #e5007e;
    --leaf-light: #eaf7a0;
    --leaf-mid: #c9ea4e;
    --leaf-deep: #7cbf2a;
    --organic-green: #5ba32e;
    --petal: #b9a7e0;
  }
  html, body { margin: 0; padding: 0; overflow: hidden; }
  body { width: 1200px; height: 316px; background: var(--paper); font-family: "Arimo", Arial, sans-serif; color: var(--ink); }
  .label { position: relative; width: 1200px; height: 316px; overflow: hidden; }

  .art-left {
    position: absolute; left: 43px; top: 27px; width: 574px; height: 276px;
    background: radial-gradient(ellipse at 75% 110%, var(--leaf-deep) 0%, transparent 45%),
                linear-gradient(100deg, var(--leaf-mid) 0%, var(--leaf-light) 45%, #f3f9d8 75%, #ffffff 100%);
  }
  .art-right {
    position: absolute; left: 857px; top: 27px; width: 160px; height: 276px;
    background: radial-gradient(circle at 70% 22%, var(--petal) 0%, #e8e2f5 30%, transparent 55%),
                radial-gradient(ellipse at 45% 100%, var(--leaf-deep) 0%, var(--leaf-mid) 30%, transparent 60%),
                linear-gradient(180deg, #ffffff 0%, #f2f8e4 100%);
  }
  .cut-line { position: absolute; left: 43px; top: 44px; width: 1147px; height: 243px; border: 1.5px solid var(--cut-line); box-sizing: border-box; }

  .maker-info { position: absolute; left: 60px; top: 50px; width: 150px; font-size: 8.6px; line-height: 9.4px; }
  .maker-info .heading { font-weight: 700; }
  .maker-info .warning { margin-top: 6px; }
  .maker-info .best-before { font-size: 5.5px; font-weight: 700; margin-top: 2px; }
  .date-box { position: absolute; left: 63px; top: 243px; width: 138px; height: 37px; background: var(--paper); }

  .usage-it { position: absolute; left: 208px; top: 48px; width: 400px; font-size: 10.4px; line-height: 17px; text-align: center; white-space: nowrap; }
  .usage-it .notice { margin-top: 10px; line-height: 14.5px; }
  .usage-it .notice-line { line-height: 14.5px; }

  .usage-de { position: absolute; left: 622px; top: 58px; width: 230px; font-size: 8.6px; line-height: 15px; text-align: center; white-space: nowrap; }
  .usage-de .lot { margin-top: 6px; font-weight: 700; }

  .pao-icon { position: absolute; left: 648px; top: 186px; }
  .organic-badge { position: absolute; left: 728px; top: 190px; width: 50px; height: 40px; background: var(--organic-green); }
  .volume { position: absolute; left: 790px; top: 200px; font-size: 19px; white-space: nowrap; }

  .maker-short { position: absolute; left: 622px; top: 248px; width: 230px; font-size: 8.8px; line-height: 15px; text-align: center; }

  .product-name { position: absolute; left: 864px; top: 138px; font-family: "Poppins", sans-serif; font-weight: 300; }
  .product-name .row { display: flex; align-items: baseline; height: 27px; }
  .product-name .main { font-size: 30px; line-height: 27px; width: 146px; }
  .product-name .quality { font-size: 20px; line-height: 27px; }

  .inside-note { position: absolute; left: 1158px; top: 158px; transform: translate(-50%, -50%) rotate(-90deg); font-size: 10px; white-space: nowrap; }
</style>
</head>
<body>
<div class="label">
  <div class="art-left" role="img" aria-label="Soft green and lime leaf swirl background"></div>
  <div class="art-right" role="img" aria-label="Illustration of a purple passion flower over green leaves"></div>
  <div class="cut-line"></div>

  <div class="maker-info">
    <div class="heading">Firmenname:</div>
    <div>Bio des Haubner Stefan</div>
    <div>Talweg 14</div>
    <div>I-39099 Valdora</div>
    <div>IVA: IT01234567890</div>
    <div>C.F.: HBNSTF80A01Z000X</div>
    <div>Tel: +39 0400/000123 Handy:</div>
    <div>3290000456</div>
    <div>https://www.natur-vemo.com/</div>
    <div>info@natur-vemo.com</div>
    <div class="warning">Nur in der angegeben Verdünnung anwenden! Nicht in die Augen oder auf die Schleimhäute bringen! Außer Reichweite von Kindern lagern. Abgefüllt in Italien</div>
    <div class="best-before">Mindestens haltbar bis:</div>
  </div>
  <div class="date-box"></div>

  <div class="usage-it">
    <div>100% olio essenziale naturale. Cosmetico aromatico per la cura del corpo.</div>
    <div>Modo d'uso: Come olio da massaggio o olio per il corpo:</div>
    <div>versare max. 15 gocce in 50ml di liquido p.es. olio di mandorla.</div>
    <div>Come bagnoschiuma: aggiungere 8-15 gocce versare nell acqua del bagno.</div>
    <div>Ingredients: Lavandula angustifolia oil, Limonene*, Linalool*, geraniol*</div>
    <div>*natürliche Bestandteile des etherischen Öls</div>
    <div>* Olio essenziale con sostanze naturali</div>
    <div class="notice">Da usare solo diluito come da indicazione!</div>
    <div class="notice-line">Evitare il contatto con occhi e mucose!</div>
    <div class="notice-line">Tenere fuori dalla portata dei bambini.</div>
    <div class="notice-line">Imbottigliato in Italy</div>
  </div>

  <div class="usage-de">
    <div>100% natürliches etherisches Öl.</div>
    <div>Aroma-Kosmetikum zur Körperpflege</div>
    <div><b>Anwendung:</b> Als Haut- u. Massageöl max 15 Tr.</div>
    <div>Mit 50 ml z.B. Mandelöl mischen.</div>
    <div>Als Badezusatz 8-15 Tr. Auf 4 Eßl. Sahne oder</div>
    <div>Milch ins Badewasser geben.</div>
    <div class="lot">Lotto: XXXXXXX</div>
  </div>

  <svg class="pao-icon" width="40" height="42" viewBox="0 0 40 42" aria-hidden="true">
    <path d="M6 12 L28 4 L30 9 L8 17 Z" fill="none" stroke="#1a1a1a" stroke-width="2"/>
    <path d="M6 20 H34 V36 Q34 38 32 38 H8 Q6 38 6 36 Z" fill="none" stroke="#1a1a1a" stroke-width="2"/>
    <text x="20" y="22" font-size="6" text-anchor="middle" font-family="Arimo, sans-serif">12M</text>
  </svg>
  <div class="organic-badge" aria-hidden="true"></div>
  <div class="volume">10 ml</div>

  <div class="maker-short">
    <div>Bio des Haubner Stefan</div>
    <div>I-39099 Valdora</div>
  </div>

  <div class="product-name">
    <div class="row"><span class="main">Lavedel</span><span class="quality">Fein</span></div>
    <div class="row"><span class="main">Lavanda</span><span class="quality">Vera</span></div>
  </div>

  <div class="inside-note">Innenseite beachten</div>
</div>
</body>
</html>
```